TOP NOTCH CATALOG RE-DESIGN FOR A NATIONAL BRAND

This Project needs to be redesigned with a new look and feel we will use all the same tires and keep the same writing we will only change the model numbers from QZ to VR then the number
please visit www.valmortires.com for feel of site which will direct your imagination

Target Market(s)

Our Target Market is Truck Drivers throughout the USA

Industry/Entity Type

Trucking Company

Font styles to use
Serif

Requirements
Must have
• Yellow and Black this signify our Brand see attached Logo
Nice to have
• Lion since our logo is that shows a strong product
Should not have
• other tires other than what is listed

```html
<!DOCTYPE html>
<html lang="en">
<head>
<meta charset="utf-8">
<title>Valmor Tires Catalog Cover</title>
<link rel="stylesheet" href="https://fonts.googleapis.com/css2?family=Roboto+Slab:wght@300;400;700;900&display=swap">
<style>
  :root {
    --backdrop: #9a9a9a;
    --paper: #f7f7f7;
    --ink: #111111;
    --muted: #555555;
    --title-grey: #6b6b6b;
    --brand-orange: #e2661c;
    --brand-yellow: #e5b30f;
    --pale-yellow: #f3d27a;
    --white: #ffffff;
  }
  * { box-sizing: border-box; margin: 0; padding: 0; }
  html, body { width: 1200px; height: 804px; overflow: hidden; }
  body {
    background: var(--backdrop);
    font-family: "Roboto Slab", Georgia, serif;
    position: relative;
  }
  .cover {
    position: absolute;
    left: 330px;
    top: 22px;
    width: 540px;
    height: 760px;
    background: var(--paper);
    overflow: hidden;
  }
  .cover-art { position: absolute; inset: 0; }
  .intro-note {
    position: absolute;
    left: 36px;
    top: 52px;
    width: 210px;
    font-size: 7.5px;
    line-height: 1.4;
    color: var(--ink);
  }
  .brand-mark {
    position: absolute;
    right: 40px;
    top: 42px;
    display: flex;
    align-items: center;
    gap: 8px;
  }
  .brand-mark .dot {
    width: 14px;
    height: 14px;
    border-radius: 50%;
    background: var(--ink);
  }
  .brand-mark .name {
    font-weight: 900;
    font-size: 17px;
    color: var(--ink);
    letter-spacing: 0.5px;
  }
  .cover-title {
    position: absolute;
    left: 0;
    right: 0;
    top: 150px;
    text-align: center;
    font-size: 44px;
    line-height: 1;
  }
  .cover-title .accent { color: var(--brand-orange); font-weight: 700; }
  .cover-title .plain { color: var(--title-grey); font-weight: 300; }
  .mission {
    position: absolute;
    left: 90px;
    right: 90px;
    top: 210px;
    text-align: center;
    font-size: 8.5px;
    line-height: 1.45;
    color: var(--muted);
  }
  .site-url {
    position: absolute;
    right: 40px;
    bottom: 30px;
    color: var(--white);
    font-size: 15px;
    letter-spacing: 1.5px;
    font-weight: 400;
  }
</style>
</head>
<body>
  <main class="cover">
    <svg class="cover-art" width="540" height="760" viewBox="0 0 540 760">
      <defs>
        <linearGradient id="stormGradient" x1="0" y1="0" x2="0" y2="1">
          <stop offset="0" stop-color="#8f7f8c"/>
          <stop offset="0.3" stop-color="#a3909a"/>
          <stop offset="0.6" stop-color="#5f7d8a"/>
          <stop offset="1" stop-color="#2c3a46"/>
        </linearGradient>
      </defs>
      <polygon class="stripe-pale" fill="var(--pale-yellow)" points="0,418 170,352 540,398 540,408 170,362 0,428"/>
      <polygon class="stripe-yellow" fill="var(--brand-yellow)" points="0,430 170,366 540,410 540,418 170,374 0,438"/>
      <polygon class="hero-photo" fill="url(#stormGradient)" role="img"
        aria-label="Photo of a truck tire standing upright in water between crashing waves under a stormy sky"
        points="0,442 170,378 540,422 540,556 228,712 0,688"/>
      <polygon class="band-orange" fill="var(--brand-orange)" points="0,688 228,712 540,556 540,572 228,728 0,704"/>
      <polygon class="band-pale" fill="var(--pale-yellow)" points="0,704 228,728 540,572 540,578 228,734 0,710"/>
      <polygon class="band-yellow" fill="var(--brand-yellow)" points="0,722 228,746 540,590 540,760 0,760"/>
    </svg>

    <p class="intro-note">At Valmor Tires, we always want to ensure that the tires are always compatible with your vehicle needs.</p>

    <div class="brand-mark">
      <span class="dot"></span>
      <span class="name">VALMOR TIRES</span>
    </div>

    <h1 class="cover-title"><span class="accent">Valmor</span> <span class="plain">Tires</span></h1>

    <p class="mission">At Valmor Tires our mission is to earn and develop long lasting relationships with our customers and business partners, through responsive actions, a dedication to quality and the highest standard of manufacturing.</p>

    <p class="site-url">www.valmortires.com</p>
  </main>
</body>
</html>
```